Website Redesign for MarrowArc.co.za – Bold, Modern & Professional Tattoo Supply Store (B2B ...

We’re looking for a skilled and creative web designer to redesign MarrowArc.co.za, a leading tattoo equipment and supplies store based in South Africa. The business serves both B2B (tattoo studios, artists, wholesalers) and B2C (individual customers) markets.

The current website is outdated and lacks the modern, edgy look that reflects the tattoo industry. We want a fresh, bold, and professional design that appeals to both professional artists and retail customers — combining trust, style, and functionality.

About the Business:
Marrow Arc supplies a wide range of tattoo-related products, including machines, needles, inks, hygiene supplies, and accessories. The company is well-established in the South African market and serves both individual tattoo artists and studios, as well as end customers looking for quality equipment.

The website must reflect the creative, bold, and artistic nature of the tattoo industry, while still being easy to navigate, fast, and conversion-focused.

What We’re Looking For:
A bold, modern design with a clear structure
Strong visual identity that reflects the tattoo culture — edgy, artistic, but still clean and professional
A layout that works for both B2B and B2C audiences
Clear product presentation and strong CTAs (Buy Now, Request Quote, Contact, etc.)
Fully responsive design (desktop + mobile)
Easy-to-navigate product categories and filters
Space for featured products, promotions, and artist-focused content
Integration of trust elements (payment icons, reviews, certifications, etc.)

Pages We Need Designed:
Homepage
Product detail page

Inspiration / Style Direction:
We’re looking for something with a strong personality, inspired by tattoo culture, but still clean and user-friendly. Think:

Dark theme with bold highlights (but open to light themes if well executed)
High-quality visuals and product imagery

Examples for inspiration:
GrimQuill.co.uk
Wexley RPN
Corvane Needle Supply
Brisk Tallow

Deliverables:
Full desktop and mobile designs (Figma, XD, or PSD)
All design source files
Fonts, icons, and assets used
Clearly labeled layers and organized files
Ready for development handoff

Target Market(s)

MarrowArc.co.za targets both B2B and B2C customers in South Africa: B2B: Professional tattoo artists, studios, and wholesalers looking for high-quality, reliable equipment and bulk pricing. B2C: Individual customers, hobbyists, and beginners seeking safe, affordable tattoo supplies with guidance and support. The site should appeal to both experienced professionals and newcomers, combining a bold, authentic tattoo vibe with a clean, user-friendly shopping experience.

Industry/Entity Type

Tattoo Equipment & Supplies – E-commerce (B2B & B2C)

Number of Pages Required

2 page

Requirements
Must have
• Responsive design, bold tattoo-inspired visual style, clear navigation for B2B & B2C, strong product presentation, clear call-to-actions, trust elements (reviews, badges, payment icons), category filters & search, dedicated B2B/wholesale info page, speed-optimized layout, easy access to contact & support.
Should not have
• Overly complex animations, cluttered layout, generic stock images, too many fonts or colors, hidden navigation, auto-play videos or sounds, outdated visual styles, low-quality product images, confusing checkout process, unnecessary pop-ups.

```html
<!DOCTYPE html>
<html lang="en">
<head>
<meta charset="utf-8">
<title>MarrowArc – Tattoo Supplies</title>
<link href="https://fonts.googleapis.com/css2?family=Unbounded:wght@700;800;900&family=Poppins:wght@400;500;600;700&display=swap" rel="stylesheet">
<style>
:root{
  --red:#9c0f2b;
  --red-dark:#6e0a1e;
  --black:#000;
  --ink:#0b0b0b;
  --line:#2e2e2e;
  --white:#fff;
  --gold:#f2a91d;
  --green:#6cc51c;
  --head:'Unbounded',sans-serif;
  --body:'Poppins',sans-serif;
}
*{box-sizing:border-box;margin:0;padding:0}
html,body{width:1200px;height:4351px;overflow:hidden}
body{background:var(--black);color:var(--white);font-family:var(--body);position:relative}
a{color:inherit;text-decoration:none}
.wrap{width:912px;margin:0 auto;position:relative}

/* header */
.topbar{height:76px;display:flex;align-items:center;padding:0 16px;position:relative}
.logo{font-family:var(--head);font-weight:800;font-size:22px;letter-spacing:1px;color:var(--white);display:flex;align-items:center;gap:8px}
.logo .dot{width:14px;height:14px;border-radius:50%;background:var(--red)}
.search{position:absolute;left:485px;top:17px;width:360px;height:37px;border:1px solid #444;border-radius:20px;display:flex;align-items:center;justify-content:space-between;padding:0 16px;font-size:11px;color:#ddd}
.callus{position:absolute;left:893px;top:17px;display:flex;align-items:center;gap:12px}
.callus .ring{width:38px;height:38px;border-radius:50%;background:var(--red);display:flex;align-items:center;justify-content:center}
.callus small{display:block;font-size:10px;color:#ddd}
.callus strong{display:block;font-size:18px;color:var(--red);font-weight:600;letter-spacing:.5px;line-height:1.1}
.usericons{position:absolute;right:14px;top:24px;display:flex;gap:12px}

.mainnav{height:42px;display:flex;align-items:center;justify-content:space-between;padding-right:14px;font-size:14px;font-weight:500}
.mainnav a{padding:0 14px;height:42px;line-height:42px}
.mainnav a.special{background:var(--red)}

/* hero */
.hero{height:495px;position:relative;overflow:hidden;background:linear-gradient(90deg,#121212 0%,#1c1c1e 45%,#2a2a2c 100%)}
.hero-visual{position:absolute;right:0;top:0;width:520px;height:495px;background:
  radial-gradient(ellipse 90px 110px at 62% 22%,#8a6a58 0%,rgba(138,106,88,0) 100%),
  radial-gradient(ellipse 220px 200px at 60% 65%,#2f4a78 0%,rgba(47,74,120,0) 100%),
  radial-gradient(ellipse 160px 90px at 55% 78%,#6c5a50 0%,rgba(108,90,80,0) 100%),
  linear-gradient(90deg,#1c1c1e,#2b2d31)}
.hero-bottles{position:absolute;left:650px;top:300px;width:270px;height:195px;background:
  linear-gradient(90deg,rgba(0,0,0,0) 0 2%,#111 2% 30%,rgba(0,0,0,0) 30% 40%,#0b0b0b 40% 100%);
  border-radius:6px 6px 0 0}
.hero-copy{position:absolute;left:144px;top:94px}
.hero-eyebrow{font-size:17px;font-weight:500}
.hero-title{font-family:var(--head);font-weight:900;font-size:58px;letter-spacing:2px;margin-top:18px;line-height:1}
.hero-title em{font-style:normal;color:var(--red)}
.hero-rule{width:470px;height:2px;background:var(--red);margin-top:28px}
.hero-sub{font-size:30px;font-weight:400;margin-top:26px;letter-spacing:.5px}
.hero-ctas{display:flex;gap:10px;margin-top:40px}
.btn{display:inline-flex;align-items:center;justify-content:center;height:51px;border-radius:26px;font-weight:700;font-size:15px;padding:0 28px;text-transform:uppercase}
.btn-red{background:var(--red)}
.btn-outline{border:2px solid var(--red);color:var(--white)}

.trust{height:41px;background:var(--red);display:flex;align-items:center;justify-content:space-between;padding:0 145px;font-size:13px}
.trust span{display:flex;align-items:center;gap:6px}

/* sections */
.section-title{font-family:var(--head);font-weight:800;font-size:32px;letter-spacing:2px;text-align:center;text-transform:uppercase}
.title-rule{width:100px;height:3px;background:var(--red);margin:16px auto 0}
.arrow{position:absolute;width:20px;height:20px}
.arrow.left{left:-50px}.arrow.right{right:-50px}

.prod-block{position:absolute;left:0;width:1200px}
.cat-row{display:flex;gap:15px;margin-top:35px;justify-content:center}
.cat{width:172px;height:191px;border:1px solid var(--line);border-radius:10px;padding:6px;background:var(--ink);text-align:center}
.cat .pic{height:145px;border-radius:6px}
.cat p{font-size:14px;margin-top:12px}
.cat.active{background:var(--red);border-color:var(--red)}

.prod-row{display:flex;gap:17px;margin-top:42px}
.card{width:215px;height:319px;border:1px solid var(--line);border-radius:10px;padding:7px;background:var(--ink);text-align:center;position:relative}
.card .pic{height:168px;border-radius:6px;position:relative}
.card .tag{position:absolute;left:6px;top:6px;background:var(--green);color:#fff;font-size:9px;font-weight:600;padding:2px 8px;border-radius:8px}
.card .tag.new{background:var(--gold)}
.card h4{font-size:13px;font-weight:500;margin-top:22px}
.card .price{font-size:15px;font-weight:600;margin-top:8px}
.card .price s{color:#bbb;font-weight:500;margin-right:8px}
.card .price b{color:var(--gold);font-weight:600}
.card .add{display:block;margin:16px auto 0;width:191px;height:37px;line-height:37px;border-radius:20px;background:var(--red);font-size:13px;font-weight:700}
.card.active{background:var(--red);border-color:var(--red)}
.card.active .add{background:#fff;color:var(--red)}
.card .tools{position:absolute;right:8px;top:10px;display:flex;flex-direction:column;gap:6px}
.card .tools i{width:18px;height:18px;border-radius:50%;border:1px solid #222;background:#fff;display:block}

/* image fills in main tones */
.img-white-ink{background:radial-gradient(ellipse 26% 45% at 50% 55%,#1a1a1a 0%,#555 60%,rgba(255,255,255,0) 100%),#fff}
.img-tape{background:radial-gradient(ellipse 45% 30% at 50% 45%,#111 0%,#333 60%,rgba(255,255,255,0) 100%),linear-gradient(180deg,#fff,#e9e9e9)}
.img-needle{background:radial-gradient(ellipse 30% 35% at 50% 50%,#4fb59a 0%,#7fc8d8 50%,rgba(255,255,255,0) 100%),#fff}
.img-stool{background:radial-gradient(ellipse 35% 40% at 50% 45%,#141414 0%,#8d8d8d 60%,rgba(255,255,255,0) 100%),#fff}
.img-machines{background:radial-gradient(ellipse 40% 30% at 50% 50%,#2b2b2b 0%,#b0232d 45%,rgba(255,255,255,0) 100%),#fff}
.img-reel{background:radial-gradient(ellipse 48% 32% at 50% 50%,#8fc9e6 0%,#b8def0 55%,rgba(255,255,255,0) 100%),#f4f9fc}
.img-blackink{background:radial-gradient(ellipse 35% 45% at 50% 50%,#0d0d0d 0%,#3a3a3a 55%,rgba(255,255,255,0) 100%),#fff}
.img-grips{background:radial-gradient(ellipse 45% 35% at 50% 50%,#1b1b1b 0%,#6a6a6a 55%,rgba(255,255,255,0) 100%),#fff}
.img-blueink{background:radial-gradient(ellipse 24% 45% at 50% 55%,#4a6d9a 0%,#e0a93a 50%,rgba(255,255,255,0) 100%),#fff}
.img-cartridge{background:radial-gradient(ellipse 40% 35% at 50% 45%,#6bb3e0 0%,#b7dcf2 55%,rgba(255,255,255,0) 100%),#fff}
.img-box{background:radial-gradient(ellipse 25% 45% at 50% 50%,#1e3466 0%,#3f6aa0 50%,rgba(255,255,255,0) 100%),#fff}
.img-glove{background:radial-gradient(ellipse 30% 45% at 50% 50%,#0c0c0c 0%,#2c2c2c 55%,rgba(255,255,255,0) 100%),#fff}
.img-cups{background:radial-gradient(ellipse 42% 35% at 50% 50%,#c9d7dc 0%,#e4ecef 55%,rgba(255,255,255,0) 100%),#fff}
.img-cabinet{background:radial-gradient(ellipse 38% 38% at 45% 55%,#0f0f0f 0%,#444 55%,rgba(255,255,255,0) 100%),#fff}
.img-sleeves{background:radial-gradient(ellipse 45% 25% at 50% 55%,#d7ac7b 0%,#e6c9a3 55%,rgba(255,255,255,0) 100%),#fff}
.img-roll{background:radial-gradient(ellipse 45% 20% at 50% 50%,#e0e0e0 0%,#f0eded 55%,rgba(255,255,255,0) 100%),#fff}
.img-spray{background:radial-gradient(ellipse 35% 42% at 45% 55%,#d83544 0%,#f0c7cb 55%,rgba(255,255,255,0) 100%),#fff}

/* about */
.about{position:absolute;top:1575px;left:0;width:1200px;height:416px;display:flex}
.about-photo{width:647px;height:416px;background:
  radial-gradient(ellipse 150px 200px at 22% 45%,#b49a80 0%,rgba(180,154,128,0) 100%),
  radial-gradient(ellipse 200px 180px at 62% 55%,#4b5a6c 0%,rgba(75,90,108,0) 100%),
  linear-gradient(120deg,#4a4440 0%,#2b2826 55%,#1b1b1c 100%)}
.about-copy{flex:1;background:var(--red);padding:52px 54px}
.about-copy h2{font-family:var(--head);font-weight:800;font-size:34px;letter-spacing:2px}
.about-copy .bar{width:130px;height:3px;background:#fff;margin-top:12px}
.about-copy p{font-size:14px;line-height:24px;margin-top:34px;max-width:370px}
.about-copy .btn{margin-top:34px;height:42px;background:#fff;color:var(--red);font-size:13px;padding:0 24px}

/* registration */
.register{position:absolute;top:3045px;left:0;width:1200px;height:320px;background:linear-gradient(100deg,#7e0b22 0%,#a0112d 50%,#860b23 100%);text-align:center;padding-top:58px}
.register .title-rule{background:#fff;margin-top:14px}
.register p{font-size:13.5px;line-height:24px;width:930px;margin:28px auto 0}
.register .btn{margin-top:22px;height:42px;background:#fff;color:var(--red);font-size:13px}

/* reviews */
.reviews{position:absolute;top:3450px;left:0;width:1200px}
.review-row{display:flex;gap:27px;justify-content:center;margin-top:42px}
.review{width:442px;height:226px;border:1px solid var(--line);border-radius:10px;display:flex;padding:8px 8px 8px 24px;background:var(--ink)}
.review .txt{flex:1;padding-top:20px;font-size:14px;line-height:24px;padding-right:20px}
.review .who{display:flex;align-items:center;gap:12px;margin-top:26px}
.review .av{width:40px;height:40px;border-radius:50%;background:linear-gradient(180deg,#6e6e6e,#3a3a3a);position:relative}
.review .av::after{content:"";position:absolute;right:-8px;bottom:-2px;width:20px;height:20px;border-radius:50%;background:var(--red);border:2px solid #111}
.review .who b{display:block;font-weight:500;font-size:16px}
.review .who small{display:block;font-size:10px;color:var(--red)}
.review .photo{width:164px;height:210px;border-radius:6px}
.photo-m{background:radial-gradient(ellipse 60px 70px at 50% 35%,#8a6d5c 0%,rgba(138,109,92,0) 100%),linear-gradient(180deg,#3d3d3d,#151515)}
.photo-f{background:radial-gradient(ellipse 60px 70px at 45% 35%,#b88b70 0%,rgba(184,139,112,0) 100%),linear-gradient(180deg,#5a4a3e,#1d1a18)}
.dots{display:flex;gap:6px;justify-content:center;margin-top:38px}
.dots i{width:20px;height:3px;background:#fff;display:block}
.dots i.on{background:var(--red)}

/* footer */
.footer{position:absolute;top:3880px;left:0;width:1200px;height:471px;border-top:1px solid #1a1a1a}
.fcol{position:absolute;top:48px}
.fcol h5{font-size:16px;font-weight:500;color:var(--red);margin-bottom:10px}
.fcol a{display:block;font-size:13.5px;line-height:27px}
.fcol h5.later{margin-top:26px}
.contact-item{display:flex;gap:10px;margin-bottom:10px}
.contact-item small{display:block;font-size:10px;font-weight:600}
.contact-item span{font-size:13.5px}
.fcol h6{font-size:16px;font-weight:500;margin-top:24px}
.social{display:flex;gap:10px;margin-top:14px}
.social i{width:28px;height:28px;border-radius:50%;background:#fff;display:block}
.footline{position:absolute;top:390px;left:144px;width:912px;height:1px;background:#2a2a2a}
.copyright{position:absolute;top:400px;width:1200px;text-align:center;font-size:13px}
.payments{position:absolute;top:432px;left:0;width:1200px;display:flex;gap:5px;justify-content:center}
.payments span{background:#fff;color:#111;font-family:var(--body);font-size:8px;font-weight:600;width:35px;height:22px;border-radius:3px;display:flex;align-items:center;justify-content:center}
</style>
</head>
<body>

<header class="topbar">
  <a class="logo" href="#"><span class="dot"></span>MarrowArc</a>
  <div class="search"><span>What are you looking for?</span>
    <svg width="14" height="14" viewBox="0 0 24 24"><circle cx="10" cy="10" r="7" fill="none" stroke="#fff" stroke-width="3"/><path d="M15 15l6 6" stroke="#fff" stroke-width="3"/></svg>
  </div>
  <div class="callus">
    <span class="ring"><svg width="18" height="18" viewBox="0 0 24 24"><path d="M6 2l4 4-2 3c1 3 4 6 7 7l3-2 4 4-3 4C10 21 3 14 2 5z" fill="#fff"/></svg></span>
    <span><small>Call Us Now</small><strong>0820005417</strong></span>
  </div>
  <div class="usericons">
    <svg width="22" height="20" viewBox="0 0 24 22"><path d="M12 20S2 13 2 7a5 5 0 0 1 10-1 5 5 0 0 1 10 1c0 6-10 13-10 13z" fill="none" stroke="#fff" stroke-width="2"/></svg>
    <svg width="20" height="20" viewBox="0 0 24 24"><circle cx="12" cy="8" r="5" fill="none" stroke="#fff" stroke-width="2"/><path d="M3 23c0-5 4-8 9-8s9 3 9 8" fill="none" stroke="#fff" stroke-width="2"/></svg>
    <svg width="22" height="20" viewBox="0 0 24 22"><path d="M1 2h4l3 13h12l3-9H7" fill="none" stroke="#fff" stroke-width="2"/><circle cx="9" cy="19" r="2" fill="#fff"/><circle cx="18" cy="19" r="2" fill="#fff"/></svg>
  </div>
</header>

<nav class="mainnav">
  <a class="special" href="#">Special</a><a href="#">Tattoo Ink</a><a href="#">Medical Supplies</a><a href="#">Needles</a><a href="#">Furniture</a><a href="#">Accessories</a><a href="#">Consumables</a><a href="#">Machines</a><a href="#">Piercing</a><a href="#">Expired Products</a><a href="#">Blog</a>
</nav>

<section class="hero">
  <div class="hero-visual" role="img" aria-label="Tattooed bearded artist in a denim shirt with arms crossed"></div>
  <div class="hero-bottles" role="img" aria-label="Two black bottles of premium tattoo ink"></div>
  <div class="hero-copy">
    <p class="hero-eyebrow">Noctra Premium Tattoo Ink Deep 8oz Bottle - Black Tattoo Inks</p>
    <h1 class="hero-title">UP TO <em>50%</em> OFF</h1>
    <div class="hero-rule"></div>
    <p class="hero-sub">PLUS 20% OFF EVERYTHING ELSE</p>
    <div class="hero-ctas"><a class="btn btn-red" href="#">Buy Now</a><a class="btn btn-outline" href="#">Request A Quote</a></div>
  </div>
</section>

<div class="trust">
  <span><svg width="11" height="12" viewBox="0 0 12 14"><path d="M6 0l6 2v5c0 4-3 6-6 7-3-1-6-3-6-7V2z" fill="#fff"/></svg>Secure Payments</span>
  <span><svg width="14" height="11" viewBox="0 0 16 12"><path d="M0 1h10v8H0zM10 4h3l3 3v2h-6z" fill="#fff"/><circle cx="3" cy="10" r="2" fill="#fff"/><circle cx="12" cy="10" r="2" fill="#fff"/></svg>Fast Shipping</span>
  <span><svg width="13" height="11" viewBox="0 0 14 12"><path d="M3 0h8l3 4-7 8-7-8z" fill="#fff"/></svg>Extensive Stock Range</span>
</div>

<section class="prod-block" style="top:725px">
  <h2 class="section-title">Shop All Categories</h2>
  <div class="title-rule"></div>
  <div class="wrap">
    <svg class="arrow left" viewBox="0 0 20 20" style="top:123px"><path d="M13 3l-7 7 7 7" fill="none" stroke="#888" stroke-width="2"/></svg>
    <svg class="arrow right" viewBox="0 0 20 20" style="top:123px"><path d="M7 3l7 7-7 7" fill="none" stroke="var(--red)" stroke-width="2"/></svg>
    <div class="cat-row">
      <div class="cat"><div class="pic img-white-ink" role="img" aria-label="White tattoo ink bottle"></div><p>Tattoo Ink</p></div>
      <div class="cat"><div class="pic img-tape" role="img" aria-label="Rolls of black medical tape"></div><p>Medical Supplies</p></div>
      <div class="cat active"><div class="pic img-needle" role="img" aria-label="Tattoo needle cartridge"></div><p>Needles</p></div>
      <div class="cat"><div class="pic img-stool" role="img" aria-label="Black studio stool"></div><p>Furniture</p></div>
      <div class="cat"><div class="pic img-machines" role="img" aria-label="Tattoo machines in cases"></div><p>Machines</p></div>
    </div>
  </div>
</section>

<section class="prod-block" style="top:1078px">
  <h2 class="section-title">Featured Products</h2>
  <div class="title-rule"></div>
  <div class="wrap">
    <svg class="arrow left" viewBox="0 0 20 20" style="top:230px"><path d="M13 3l-7 7 7 7" fill="none" stroke="#888" stroke-width="2"/></svg>
    <svg class="arrow right" viewBox="0 0 20 20" style="top:230px"><path d="M7 3l7 7-7 7" fill="none" stroke="var(--red)" stroke-width="2"/></svg>
    <div class="prod-row">
      <div class="card"><div class="pic img-reel" role="img" aria-label="Rolls of sterilisation pouch reel"><span class="tag">20% OFF</span></div><h4>Cleanreel 100 Mm X 100m</h4><p class="price"><s>$90.00</s><b>$80.00</b></p><a class="add" href="#">ADD TO CART</a></div>
      <div class="card"><div class="pic img-blackink" role="img" aria-label="Black tattoo ink bottle"></div><h4>Umbra Deep Tattoo Ink ...</h4><p class="price"><s>$90.00</s><b>$80.00</b></p><a class="add" href="#">ADD TO CART</a></div>
      <div class="card active"><div class="pic img-grips" role="img" aria-label="Disposable silica gel tattoo grips"><span class="tools"><i></i><i></i><i></i></span></div><h4>Disposable Silica Gel Grip</h4><p class="price"><s>$90.00</s><b>$80.00</b></p><a class="add" href="#">ADD TO CART</a></div>
      <div class="card"><div class="pic img-blueink" role="img" aria-label="Blue tattoo ink bottle"><span class="tag">20% OFF</span></div><h4>Solace Tattoo Ink ...</h4><p class="price"><s>$90.00</s><b>$80.00</b></p><a class="add" href="#">ADD TO CART</a></div>
    </div>
  </div>
</section>

<section class="about">
  <div class="about-photo" role="img" aria-label="Tattoo artist in gloves working on a client's arm"></div>
  <div class="about-copy">
    <h2>ABOUT US</h2>
    <div class="bar"></div>
    <p>Marrow Arc supplies a wide range of tattoo-related products, including machines, needles, inks, hygiene supplies, and accessories. The company is well established in the South African market and serves both individual tattoo artists and studios, as well as end customers looking for quality equipment.</p>
    <a class="btn" href="#">Contact Us</a>
  </div>
</section>

<section class="prod-block" style="top:2078px">
  <h2 class="section-title">Bestsellers</h2>
  <div class="title-rule"></div>
  <div class="wrap">
    <svg class="arrow left" viewBox="0 0 20 20" style="top:230px"><path d="M13 3l-7 7 7 7" fill="none" stroke="#888" stroke-width="2"/></svg>
    <svg class="arrow right" viewBox="0 0 20 20" style="top:230px"><path d="M7 3l7 7-7 7" fill="none" stroke="var(--red)" stroke-width="2"/></svg>
    <div class="prod-row">
      <div class="card"><div class="pic img-cartridge" role="img" aria-label="Blue tattoo liner cartridge"></div><h4>KVR Tattoo Liner Cartrid...</h4><p class="price"><s>$90.00</s><b>$80.00</b></p><a class="add" href="#">ADD TO CART</a></div>
      <div class="card"><div class="pic img-box" role="img" aria-label="Boxed ultra liner cartridges"></div><h4>KVR Ultra Liners</h4><p class="price"><s>$90.00</s><b>$80.00</b></p><a class="add" href="#">ADD TO CART</a></div>
      <div class="card"><div class="pic img-glove" role="img" aria-label="Black nitrile glove"><span class="tag">20% OFF</span></div><h4>Ironpalm Black...</h4><p class="price"><s>$90.00</s><b>$80.00</b></p><a class="add" href="#">ADD TO CART</a></div>
      <div class="card"><div class="pic img-cups" role="img" aria-label="Clear plastic ink cups"></div><h4>Ink Cups Stable Ø 10mm...</h4><p class="price"><s>$90.00</s><b>$80.00</b></p><a class="add" href="#">ADD TO CART</a></div>
    </div>
  </div>
</section>

<section class="prod-block" style="top:2566px">
  <h2 class="section-title">Latest Products</h2>
  <div class="title-rule"></div>
  <div class="wrap">
    <svg class="arrow left" viewBox="0 0 20 20" style="top:230px"><path d="M13 3l-7 7 7 7" fill="none" stroke="#888" stroke-width="2"/></svg>
    <svg class="arrow right" viewBox="0 0 20 20" style="top:230px"><path d="M7 3l7 7-7 7" fill="none" stroke="var(--red)" stroke-width="2"/></svg>
    <div class="prod-row">
      <div class="card"><div class="pic img-cabinet" role="img" aria-label="Black UV sterilising cabinet"><span class="tag new">New</span></div><h4>UV Cabinet Large for...</h4><p class="price"><s>$90.00</s><b>$80.00</b></p><a class="add" href="#">ADD TO CART</a></div>
      <div class="card"><div class="pic img-sleeves" role="img" aria-label="Box of compostable pen machine sleeves"><span class="tag new">New</span></div><h4>Elite Compostable Pen...</h4><p class="price"><s>$90.00</s><b>$80.00</b></p><a class="add" href="#">ADD TO CART</a></div>
      <div class="card"><div class="pic img-roll" role="img" aria-label="Roll of non woven wrap"><span class="tag new">New</span></div><h4>Softwrap Non Woven...</h4><p class="price"><s>$90.00</s><b>$80.00</b></p><a class="add" href="#">ADD TO CART</a></div>
      <div class="card"><div class="pic img-spray" role="img" aria-label="Hypochlorous spray bottle and box"><span class="tag new">New</span></div><h4>Veluma Hypochlorous...</h4><p class="price"><s>$90.00</s><b>$80.00</b></p><a class="add" href="#">ADD TO CART</a></div>
    </div>
  </div>
</section>

<section class="register">
  <h2 class="section-title">Registration</h2>
  <div class="title-rule"></div>
  <p>At MarrowArc we like to ensure that the tattoo industry standards are maintained, and if you are in this industry we are sure that you will welcome our registration process. Therefore we only supply to studios and artist that comply to legislation, and local bylaws. Please provide us with the following information to enable us to approve your registration request.</p>
  <a class="btn" href="#">Register Account</a>
</section>

<section class="reviews">
  <h2 class="section-title">Customer Reviews</h2>
  <div class="title-rule"></div>
  <div class="review-row">
    <div class="review">
      <div class="txt">Lorem ipsum dolor sit amet, consectetur adipiscing elit, sed do eiusmod tempor incididunt ut labore et dolore
        <div class="who"><span class="av" role="img" aria-label="Customer avatar"></span><span><b>Rian Vos</b><small>Lorem ipsum dolor</small></span></div>
      </div>
      <div class="photo photo-m" role="img" aria-label="Portrait of a tattooed male customer"></div>
    </div>
    <div class="review">
      <div class="txt">Lorem ipsum dolor sit amet, consectetur adipiscing elit, sed do eiusmod tempor incididunt ut labore et dolore
        <div class="who"><span class="av" role="img" aria-label="Customer avatar"></span><span><b>Lerato Mokoena</b><small>Lorem ipsum dolor</small></span></div>
      </div>
      <div class="photo photo-f" role="img" aria-label="Portrait of a smiling female tattoo artist"></div>
    </div>
  </div>
  <div class="dots"><i class="on"></i><i></i><i></i></div>
</section>

<footer class="footer">
  <div class="fcol" style="left:144px">
    <h5>User Account</h5>
    <a href="#">My Account</a><a href="#">Wishlist</a><a href="#">Compare</a><a href="#">Returns</a><a href="#">Specials</a><a href="#">Search</a><a href="#">Order History</a><a href="#">Newsletter</a><a href="#">Shopping Cart</a><a href="#">Checkout</a><a href="#">Logout</a>
  </div>
  <div class="fcol" style="left:316px">
    <h5>Information</h5>
    <a href="#">Track My Parcel</a><a href="#">Delivery Information</a><a href="#">About Us</a><a href="#">Privacy Policy (POPI)</a><a href="#">Terms &amp; Conditions</a><a href="#">Original Manufacturers Guarantee</a><a href="#">Cookies Policy</a><a href="#">Returns &amp; Refunds Policy</a>
  </div>
  <div class="fcol" style="left:619px">
    <h5>Customer Service</h5>
    <a href="#">Contact Us</a><a href="#">Returns</a><a href="#">Site Map</a>
    <h5 class="later">My Account</h5>
    <a href="#">Account</a><a href="#">Order History</a><a href="#">Wish List (0)</a><a href="#">Newsletter</a>
  </div>
  <div class="fcol" style="left:833px">
    <h5>Contact Us</h5>
    <div class="contact-item"><svg width="11" height="11" viewBox="0 0 24 24"><path d="M6 2l4 4-2 3c1 3 4 6 7 7l3-2 4 4-3 4C10 21 3 14 2 5z" fill="var(--red)"/></svg><div><small>TELEPHONE</small><span>0820005417</span></div></div>
    <div class="contact-item"><svg width="11" height="11" viewBox="0 0 24 24"><path d="M1 4h22v16H1z" fill="var(--red)"/></svg><div><small>EMAIL</small><span>info@marrowarc.co.za</span></div></div>
    <div class="contact-item"><svg width="11" height="12" viewBox="0 0 24 26"><path d="M12 0a9 9 0 0 1 9 9c0 7-9 17-9 17S3 16 3 9a9 9 0 0 1 9-9z" fill="var(--red)"/></svg><div><small>STORE ADDRESS</small><span>Po Box 40217 Kleinmond 7195</span></div></div>
    <h6>My Account</h6>
    <div class="social"><i></i><i></i><i></i><i></i></div>
  </div>
  <div class="footline"></div>
  <p class="copyright">Copyright© 2025 MarrowArc Pty Ltd - All Rights Reserved</p>
  <div class="payments"><span>Quorra</span><span>Benlo</span><span>Tarnik</span><span>Oxwell</span><span>Zunda</span></div>
</footer>

</body>
</html>
```